Kovát Lillas Physiotherapy Business Card Vienna

We need a business card design for a newly created Physiotherapy company based in Vienna Austria.
We seek a simple, modern, minimalist design without too much color variation. The font should look young/fresh, but definitely not childish or so. Since we are a starting Business, we currently haven't got a logo, if you feel like a logo would fit your design, feel free to use one, but it's not necessary.
Target Market(s)
Healthcare, young and elderly people with mobility issues
Industry/Entity Type
Health And Wellness
Contact Information for Business Card
Name: Lilla Kovát
Title description: Physiotherapist
Phone num: +43 664 2951 4086
e-mail: lilla.praxis@bluemail.example
Colors
Designer to choose colors to be used in the design.
Requirements
Must have
- Final design language must be in German, basically, the Title Description needs to be "Physiotherapeutin" the other details remain as in the English Language.
Nice to have
- Simple, modern, minimalist design
Should not have
- too many colors, Obvious use of a skeleton, skull, spline

```html
<!DOCTYPE html>
<html lang="de">
<head>
<meta charset="utf-8">
<title>Lilla Kovát – Physiotherapeutin</title>
<link rel="stylesheet" href="https://fonts.googleapis.com/css2?family=Saira+Extra+Condensed:wght@400;700&display=swap">
<style>
  :root {
    --backdrop: #3aa59c;
    --card: #ffffff;
    --ink: #0a0a0a;
  }
  html, body {
    margin: 0;
    padding: 0;
    width: 1200px;
    height: 1200px;
    overflow: hidden;
    background: var(--backdrop);
  }
  .business-card {
    display: block;
    width: 1200px;
    height: 1200px;
    font-family: "Saira Extra Condensed", "Arial Narrow", sans-serif;
  }
  .card-sheet { fill: var(--card); }
  .card-frame line {
    stroke: var(--ink);
    stroke-width: 6;
    stroke-linecap: round;
  }
  .headline {
    fill: var(--ink);
    font-weight: 700;
    font-size: 108px;
  }
  .person-name {
    fill: var(--ink);
    font-weight: 400;
    font-size: 56px;
  }
  .contact {
    fill: var(--ink);
    font-weight: 400;
    font-size: 46px;
  }
</style>
</head>
<body>
<svg class="business-card" viewBox="0 0 1200 1200" role="img" aria-label="Visitenkarte von Lilla Kovát, Physiotherapeutin">
  <rect class="card-sheet" x="296" y="128" width="609" height="942"/>
  <g class="card-frame">
    <line x1="320" y1="154" x2="880" y2="154"/>
    <line x1="320" y1="1046" x2="880" y2="1046"/>
    <line x1="320" y1="154" x2="320" y2="182"/>
    <line x1="320" y1="294" x2="320" y2="612"/>
    <line x1="320" y1="720" x2="320" y2="1046"/>
    <line x1="880" y1="154" x2="880" y2="414"/>
    <line x1="880" y1="522" x2="880" y2="840"/>
    <line x1="880" y1="948" x2="880" y2="1046"/>
  </g>
  <g class="headline">
    <text x="358" y="274" textLength="376" lengthAdjust="spacingAndGlyphs">PHYSIOTHE</text>
    <text x="358" y="374" textLength="328" lengthAdjust="spacingAndGlyphs">RAPEUTIN</text>
  </g>
  <text class="person-name" x="430" y="622" textLength="344" lengthAdjust="spacingAndGlyphs">LILLA KOVÁT</text>
  <g class="contact">
    <text x="358" y="844" textLength="292" lengthAdjust="spacingAndGlyphs">Physiotherapist</text>
    <text x="354" y="902" textLength="339" lengthAdjust="spacingAndGlyphs">+43 664 2951 4086</text>
    <text x="354" y="966" textLength="494" lengthAdjust="spacingAndGlyphs">lilla.praxis@bluemail.example</text>
  </g>
</svg>
</body>
</html>
```